Brightway Haul & Upkeep Services, are a company that offers a 'one stop shop' pre-move clean up a

I have already selected a logo which I would like on the front of the business cards along with phone numbers, web address and email which are:
0487650392
www.brightwayhaul.com.au
brightwayhaulandupkeep@mailbox.example

On the back of the card I would like to list some of the types of service we offer (clean - move - repairs/maintenance) which are:
CLEAN - windows, gutters, solar panels, driveways/paths, carpets.
MOVE - Small/medium size house/office moves, large item pick-up & delivery, yard clean-up and removal.
General maintenance and repairs.

I would like the blue logo on a gray background.

Thanks

```html
<!DOCTYPE html>
<html lang="en">
<head>
<meta charset="utf-8">
<title>Brightway Haul &amp; Upkeep Services – Business Cards</title>
<link href="https://fonts.googleapis.com/css2?family=Roboto+Condensed:wght@400;700&family=Ubuntu:wght@400&display=swap" rel="stylesheet">
<style>
  :root {
    --stage: #6b4128;
    --brand-blue: #1f6cba;
    --ink: #1d1d1d;
    --body-ink: #333333;
    --card-white: #ffffff;
    --card-grey: #d9d9db;
    --faint-brand: #e3e9f3;
    --label-ink: #f3e6d8;
  }
  * { box-sizing: border-box; margin: 0; padding: 0; }
  html, body { width: 1200px; height: 800px; overflow: hidden; }
  body {
    position: relative;
    background: var(--stage);
    font-family: "Roboto Condensed", "Arial Narrow", sans-serif;
  }
  .side-label {
    position: absolute;
    width: 508px;
    text-align: center;
    font-family: "Ubuntu", sans-serif;
    font-size: 22px;
    color: var(--label-ink);
  }
  .card {
    position: absolute;
    width: 508px;
    height: 291px;
    border-radius: 20px;
    overflow: hidden;
    box-shadow: 0 4px 10px rgba(0,0,0,.35);
  }
  .card--front { left: 70px; top: 90px; background: linear-gradient(135deg, #e4e4e6, var(--card-white) 60%); }
  .card--back-one { left: 620px; top: 90px; background: var(--card-grey); }
  .card--back-two { left: 72px; top: 450px; background: var(--card-white); }
  .card--back-three { left: 620px; top: 450px; background: var(--brand-blue); }

  .brand-name {
    position: absolute;
    left: 0; right: 0;
    text-align: center;
    font-weight: 700;
    font-size: 34px;
    line-height: 1.05;
    color: var(--brand-blue);
  }
  .card--back-three .brand-name { color: #ffffff; }
  .brand-name--faint {
    color: var(--faint-brand);
    font-size: 40px;
    top: 146px;
  }

  .contact {
    position: absolute;
    display: flex;
    align-items: center;
    gap: 5px;
    font-size: 13px;
    color: var(--body-ink);
    white-space: nowrap;
  }
  .contact svg { width: 10px; height: 10px; flex: none; }
  .contact--phone { left: 32px; top: 242px; }
  .contact--web { left: 32px; top: 260px; }
  .contact--email { right: 28px; top: 260px; }

  .services {
    position: absolute;
    left: 20px; right: 20px;
    text-align: center;
    font-size: 14px;
    line-height: 17px;
    color: var(--body-ink);
  }
  .services p { margin-bottom: 8px; }
  .services .service-key,
  .services .service-general { color: var(--brand-blue); font-weight: 700; }

  .services--list {
    text-align: left;
    left: 60px; right: 50px;
    color: #ffffff;
  }
  .services--list p { display: flex; }
  .services--list .service-key { color: #ffffff; width: 56px; flex: none; }
  .services--list .service-general { color: #ffffff; }

  .web-line {
    position: absolute;
    left: 0; right: 0;
    bottom: 26px;
    text-align: center;
    font-size: 14px;
    color: var(--ink);
  }
</style>
</head>
<body>

  <div class="side-label" style="left:70px; top:48px;">Front</div>
  <div class="side-label" style="left:620px; top:48px;">Back - 1</div>
  <div class="side-label" style="left:72px; top:408px;">Back - 2</div>
  <div class="side-label" style="left:620px; top:408px;">Back - 3</div>

  <section class="card card--front">
    <h1 class="brand-name" style="top:62px;">Brightway Haul<br>&amp; Upkeep Services</h1>

    <div class="contact contact--phone">
      <svg viewBox="0 0 12 12" aria-hidden="true"><circle cx="6" cy="6" r="5.2" fill="none" stroke="var(--brand-blue)" stroke-width="1.2"/><path d="M4 3.5c0 2.5 1.8 4.5 4.4 4.6l.3-1.2-1.3-.6-.6.6c-.8-.4-1.4-1-1.8-1.8l.6-.6-.6-1.3z" fill="var(--brand-blue)"/></svg>
      <span>0487650392</span>
    </div>
    <div class="contact contact--web">
      <svg viewBox="0 0 12 12" aria-hidden="true"><path d="M1 5l5-3 5 3v5H1z" fill="var(--brand-blue)"/><path d="M1 5l5 3 5-3" fill="none" stroke="#fff" stroke-width="1"/></svg>
      <span>www.brightwayhaul.com.au</span>
    </div>
    <div class="contact contact--email">
      <svg viewBox="0 0 12 12" aria-hidden="true"><circle cx="6" cy="6" r="5" fill="var(--brand-blue)"/><path d="M1 6h10M6 1c-2 2.5-2 7.5 0 10M6 1c2 2.5 2 7.5 0 10" fill="none" stroke="#fff" stroke-width=".8"/></svg>
      <span>brightwayhaulandupkeep@mailbox.example</span>
    </div>
  </section>

  <section class="card card--back-one">
    <h2 class="brand-name" style="top:60px;">Brightway Haul<br>&amp; Upkeep Services</h2>
    <div class="services" style="top:188px;">
      <p><span class="service-key">CLEAN</span> - Windows, Gutters, Solar Panels, Driveways/paths, Carpets.</p>
      <p><span class="service-key">MOVE</span> - Small/medium size house/office moves, large item pick-up &amp; delivery,<br>yard clean-up and removal.</p>
      <p class="service-general">General maintenance and repairs.</p>
    </div>
  </section>

  <section class="card card--back-two">
    <div class="brand-name brand-name--faint" aria-hidden="true">Brightway Haul<br>&amp; Upkeep Services</div>
    <div class="services" style="top:50px;">
      <p><span class="service-key">CLEAN</span> - Windows, Gutters, Solar Panels, Driveways/paths, Carpets.</p>
      <p><span class="service-key">MOVE</span> - Small/medium size house/office moves, large item pick-up &amp; delivery,<br>yard clean-up and removal.</p>
      <p class="service-general">General maintenance and repairs.</p>
    </div>
    <div class="web-line">www.brightwayhaul.com.au</div>
  </section>

  <section class="card card--back-three">
    <h2 class="brand-name" style="top:64px;">Brightway Haul<br>&amp; Upkeep Services</h2>
    <div class="services services--list" style="top:178px;">
      <p><span class="service-key">CLEAN -</span><span>Windows, Gutters, Solar Panels, Driveways/paths, Carpets.</span></p>
      <p><span class="service-key">MOVE -</span><span>Small/medium size house/office moves, large item pick-up &amp; delivery, yard clean-up and removal.</span></p>
      <p class="service-general">General maintenance and repairs.</p>
    </div>
  </section>

</body>
</html>
```